Pet sitting Business needs a website

We need a website that shows our services and prices. Shows our love of animals but also our professionalism. want a gallery, about, blog, services, links to fb and instagram accounts, newsletter archive. want it to be easy to access and wonderful to navigate. want the domain to be Birchfordpawhaven.com
take any info from FB site www.facebook.com/birchfordpawhaven
I would like it to fit square space platform

Target Market(s)

upscale area, responsible pet owners,

Industry/Entity Type

Pet Care

Coding

Coded - Design and coding required

Number of Pages Required

5+ page

Font styles to use
Sans Serif

Requirements
Must have
• (square space platform)
• Menu
• photo gallery
• about us
• services
• policies
• monthly newsletter
• unavailable dates
• Introduction (welcome)
• payment methods
• Daily updates
• testimonials (use from fb site)
Should not have
• stock photos

```html
<!DOCTYPE html>
<html lang="en">
<head>
<meta charset="utf-8">
<title>Birchford Paw Haven – Professional Pet Sitting</title>
<link href="https://fonts.googleapis.com/css2?family=Open+Sans:ital,wght@0,400;0,600;0,700;1,400&family=Raleway:wght@700&display=swap" rel="stylesheet">
<style>
:root{
  --blue:#0a7ab0;
  --orange:#e39b0c;
  --ink:#333;
  --muted:#666;
  --light:#f3f3f3;
  --white:#fff;
  --dark:#1b1b1b;
  --darker:#111;
  --footer-text:#bdbdbd;
  --grey-band:#7a7a7a;
}
*{margin:0;padding:0;box-sizing:border-box}
html,body{width:1200px;height:2332px;overflow:hidden}
body{font-family:"Open Sans",Arial,sans-serif;color:var(--ink);background:var(--white);position:relative}
.abs{position:absolute}

/* Header */
.site-header{position:absolute;left:0;top:0;width:1200px;height:152px;background:var(--white)}
.brand{left:98px;top:62px;display:flex;align-items:center;gap:10px}
.brand-mark{width:26px;height:26px;border-radius:50%;background:var(--orange)}
.brand-name{font-size:24px;font-weight:600;color:var(--orange);line-height:1}
.brand-tag{left:134px;top:96px;font-size:11px;color:var(--blue);font-weight:600}
.top-contact{right:99px;top:23px;font-size:13px;color:var(--ink)}
.top-contact .lbl{color:var(--blue)}
.top-contact .sep{margin:0 10px;color:var(--muted)}
.social{right:99px;top:66px;display:flex;gap:14px}
.social span{width:13px;height:13px;border-radius:50%;background:#444;display:block}
.main-nav{right:99px;top:104px;display:flex;gap:0;font-size:13px;text-transform:uppercase}
.main-nav a{color:var(--ink);text-decoration:none;padding:0 16px;line-height:28px;height:28px}
.main-nav a.active{background:var(--blue);color:var(--white);padding:0 13px;margin-right:18px}
.main-nav a:last-child{padding-right:0}

/* Hero */
.hero{left:0;top:151px;width:1200px;height:508px;background:linear-gradient(90deg,#2a2418 0%,#3e3626 30%,#6d5a3e 55%,#8a6d4c 75%,#5b6b3a 100%)}
.scallop-down{left:0;top:146px;width:1200px;height:12px;background:radial-gradient(circle at 6px 0,var(--white) 6px,transparent 6.5px) repeat-x;background-size:12px 12px}
.hero-title{left:100px;top:352px;color:var(--white)}
.hero-title .lead{font-size:26px;font-weight:400;display:block;line-height:32px}
.hero-title .big{font-size:42px;font-weight:700;display:block;letter-spacing:1px;line-height:50px}
.btn{display:inline-flex;align-items:center;justify-content:center;gap:7px;color:var(--white);font-weight:600;border-radius:2px;text-decoration:none}
.btn-orange{background:var(--orange)}
.btn-blue{background:var(--blue)}
.btn svg{width:13px;height:13px}
.hero-btn{left:103px;top:452px;width:130px;height:38px;font-size:15px}
.slide-arrow{top:388px;width:32px;height:32px;border-radius:50%;background:rgba(255,255,255,.35)}
.slide-arrow.prev{left:14px}
.slide-arrow.next{right:14px;background:rgba(255,255,255,.2)}
.slide-arrow svg{width:32px;height:32px}

/* Welcome */
.welcome{left:0;top:659px;width:1200px;height:421px;background:var(--light)}
.section-title{font-size:31px;font-weight:400;color:var(--ink)}
.welcome .section-title{left:0;width:1200px;text-align:center;top:40px}
.welcome-photo{left:99px;top:109px;width:324px;height:241px;background:linear-gradient(135deg,#4a3a30,#2b2624 55%,#3f8a3a)}
.welcome-copy{left:462px;top:107px;width:612px;font-size:12.4px;line-height:20px;color:#555}
.welcome-copy strong{color:var(--ink);font-weight:600}
.welcome-tagline{left:462px;top:232px;font-size:13.5px;font-weight:600;color:var(--blue)}
.welcome-more{left:462px;top:295px;width:110px;height:32px;font-size:12px}
.welcome-contact{left:577px;top:295px;width:109px;height:32px;font-size:12px}

/* Testimonials */
.testimonials{left:0;top:1080px;width:1200px;height:428px;background:var(--white)}
.testimonials .section-title{left:0;width:1200px;text-align:center;top:57px}
.avatar{width:61px;height:61px;border-radius:50%;background:linear-gradient(135deg,#a8a08e,#556b4a);border:3px solid #eee}
.quote-card{width:374px;height:161px;background:var(--white);border:2px solid var(--blue)}
.quote-card.grey{border-color:var(--grey-band)}
.quote-card .notch{position:absolute;left:-13px;top:20px;width:22px;height:22px;background:var(--white);border-left:2px solid var(--blue);border-bottom:2px solid var(--blue);transform:rotate(45deg)}
.quote-card.grey .notch{border-color:var(--grey-band)}
.quote-mark{position:absolute;left:16px;top:6px;font-size:30px;color:#bbb;font-family:Georgia,serif;line-height:1}
.quote-text{position:absolute;left:50px;top:32px;width:300px;font-size:11.6px;line-height:17.5px;font-style:italic;color:#888}
.quote-name{position:absolute;left:-2px;bottom:-2px;width:374px;height:38px;background:var(--blue);color:var(--white);font-size:14.5px;font-weight:600;padding-left:48px;line-height:38px}
.quote-card.grey .quote-name{background:var(--grey-band)}
.dots{left:580px;top:1441px;display:flex;gap:7px}
.dots span{width:6px;height:6px;border-radius:50%;background:#ccc}
.dots span.on{background:var(--blue)}

/* Gallery */
.gallery{left:0;top:1508px;width:1200px;height:400px;background:var(--light)}
.gallery .section-title{left:96px;top:40px}
.gal-arrow{top:50px;width:24px;height:24px;border-radius:50%}
.gal-arrow.prev{left:1051px;background:#e3e3e3}
.gal-arrow.next{left:1077px;background:var(--blue)}
.gal-arrow svg{width:24px;height:24px}
.gal-item{top:107px;width:240px;height:240px;background:var(--white);padding:4px}
.gal-item div{width:100%;height:100%}

/* Footer */
.site-footer{left:0;top:1914px;width:1200px;height:418px;background:var(--dark);color:var(--footer-text)}
.scallop-up{left:0;top:1902px;width:1200px;height:12px;background:radial-gradient(circle at 6px 12px,var(--dark) 6px,transparent 6.5px) repeat-x;background-size:12px 12px}
.foot-head{font-family:"Raleway",Arial,sans-serif;font-size:14px;font-weight:700;color:var(--orange);text-transform:uppercase}
.foot-rule{width:26px;height:2px;background:var(--orange)}
.foot-links{font-size:10.5px;text-transform:uppercase;color:#ddd}
.foot-links li{list-style:none;width:128px;height:33px;border-bottom:1px solid #444;padding-top:8px}
.foot-divider{top:62px;width:1px;height:238px;background:#2c2c2c}
.contact-block{left:525px;top:147px;font-size:10.5px;line-height:19.5px;color:#bbb}
.contact-block .lbl{color:var(--white);font-weight:700}
.news-copy{left:824px;top:144px;width:300px;font-size:10.5px;line-height:19px;color:#bbb}
.news-input{left:824px;top:2117px;width:240px;height:35px;background:#2a2a2a;font-size:10.5px;color:#bbb;padding-left:14px;line-height:35px}
.news-send{left:1064px;top:2117px;width:41px;height:35px;background:var(--orange)}
.news-send svg{width:41px;height:35px}
.copyright{left:99px;top:2256px;font-size:10px;color:#999}
.legal-bar{left:730px;top:2250px;width:470px;height:38px;background:var(--darker);display:flex;align-items:center;padding-left:55px;gap:22px;font-size:10px;color:#bbb}
</style>
</head>
<body>

<header class="site-header">
  <div class="abs brand"><span class="brand-mark"></span><span class="brand-name">Birchford Paw Haven</span></div>
  <div class="abs brand-tag">Headed by Lic. Vet Tech</div>
  <div class="abs top-contact"><span class="lbl">Call us on:</span> +1 (555) 014-2290<span class="sep">|</span><span class="lbl">Email:</span> hello@birchfordpawhaven.com</div>
  <div class="abs social" aria-label="Social links"><span></span><span></span><span></span><span></span><span></span><span></span></div>
  <nav class="abs main-nav">
    <a class="active">Home</a><a>About</a><a>Services</a><a>Pricing</a><a>Testimonials</a><a>News</a><a>Contacts</a>
  </nav>
</header>

<section class="abs hero" role="img" aria-label="Close-up photograph of a smiling spaniel dog outdoors"></section>
<div class="abs scallop-down"></div>
<div class="abs slide-arrow prev"><svg viewBox="0 0 32 32"><path d="M19 10l-6 6 6 6" fill="none" stroke="#222" stroke-width="2.5"/></svg></div>
<div class="abs slide-arrow next"><svg viewBox="0 0 32 32"><path d="M13 10l6 6-6 6" fill="none" stroke="#fff" stroke-width="2.5"/></svg></div>
<h1 class="abs hero-title"><span class="lead">We provide professional</span><span class="big">PET SITTING</span></h1>
<a class="abs btn btn-orange hero-btn">Read More <svg viewBox="0 0 14 14"><circle cx="7" cy="7" r="6.5" fill="#fff"/><path d="M6 4l3 3-3 3" fill="none" stroke="#e39b0c" stroke-width="1.8"/></svg></a>

<section class="abs welcome">
  <h2 class="abs section-title">Welcome To Our Site</h2>
  <div class="abs welcome-photo" role="img" aria-label="Photograph of the pet sitter cuddling a small dark dog"></div>
  <p class="abs welcome-copy"><strong>Hi my name is Marla Quenby</strong> and I would love to introduce myself. I am a Licensed Veterinarian Technician from Millbrook, Ohio. My family and I moved to Birchford in 2008. I have dedicated the last 13 years to raising my 2 beautiful children and 5 of my furry babies. I have the knowledge and the training to give the special care your pet will need. I was a Licensed Veterinarian Technician Supervisor of a major animal hospital in Millbrook. I have spent 20 years of my life taking care of our friends and would love to do the same for yours.</p>
  <p class="abs welcome-tagline">Where kisses and hugs are my speciality</p>
  <a class="abs btn btn-orange welcome-more">Read More <svg viewBox="0 0 14 14"><circle cx="7" cy="7" r="6.5" fill="#fff"/><path d="M6 4l3 3-3 3" fill="none" stroke="#e39b0c" stroke-width="1.8"/></svg></a>
  <a class="abs btn btn-blue welcome-contact">Contact Us <svg viewBox="0 0 14 14"><circle cx="7" cy="7" r="6.5" fill="#fff"/><path d="M6 4l3 3-3 3" fill="none" stroke="#0a7ab0" stroke-width="1.8"/></svg></a>
</section>

<section class="abs testimonials">
  <h2 class="abs section-title">Testimonials</h2>
  <div class="abs avatar" style="left:124px;top:155px" role="img" aria-label="Portrait of a client"></div>
  <div class="abs quote-card" style="left:213px;top:145px">
    <span class="notch"></span><span class="quote-mark">&ldquo;</span>
    <p class="quote-text">I am eternally grateful for the care and attention my pets receive from Birchford Paw Haven!! They love Marla as much as they love me! And the beautiful photography / videos are a huge plus!!</p>
    <div class="quote-name">Dana Whitlow</div>
  </div>
  <div class="abs avatar" style="left:639px;top:155px" role="img" aria-label="Portrait of a client"></div>
  <div class="abs quote-card grey" style="left:727px;top:145px">
    <span class="notch"></span><span class="quote-mark">&ldquo;</span>
    <p class="quote-text">Love Marla and her "crew"! We'd be lost without her when we leave town. Pepper and Juno are so thankful for her!</p>
    <div class="quote-name">Petra Lindvall</div>
  </div>
</section>
<div class="abs dots"><span class="on"></span><span></span><span></span><span></span></div>

<section class="abs gallery">
  <h2 class="abs section-title">Our Gallery</h2>
  <div class="abs gal-arrow prev"><svg viewBox="0 0 24 24"><path d="M14 7l-5 5 5 5" fill="none" stroke="#fff" stroke-width="2.5"/></svg></div>
  <div class="abs gal-arrow next"><svg viewBox="0 0 24 24"><path d="M10 7l5 5-5 5" fill="none" stroke="#fff" stroke-width="2.5"/></svg></div>
  <div class="abs gal-item" style="left:99px"><div role="img" aria-label="Photograph of a black and white dog on a wooden floor" style="background:linear-gradient(135deg,#c08a4a,#2a2420 50%,#a06a38)"></div></div>
  <div class="abs gal-item" style="left:352px"><div role="img" aria-label="Photograph of a tan dog sitting on a stone patio" style="background:linear-gradient(135deg,#7a6a5c,#b07a4a 50%,#6a5a50)"></div></div>
  <div class="abs gal-item" style="left:605px"><div role="img" aria-label="Photograph of a cat and a dark shaggy dog resting together" style="background:linear-gradient(135deg,#d8d4d0,#2e2824 50%,#1e1a18)"></div></div>
  <div class="abs gal-item" style="left:858px"><div role="img" aria-label="Photograph of a tabby kitten indoors" style="background:linear-gradient(135deg,#9a7048,#6e5a48 50%,#c8c4c0)"></div></div>
</section>

<div class="abs scallop-up"></div>
<footer class="abs site-footer">
  <div class="abs foot-head" style="left:99px;top:72px">Quick Links</div>
  <div class="abs foot-rule" style="left:99px;top:101px"></div>
  <ul class="abs foot-links" style="left:99px;top:140px"><li>Home</li><li>News</li><li>Quality</li><li>FAQ</li></ul>
  <ul class="abs foot-links" style="left:253px;top:140px"><li>About Us</li><li>Contact Us</li><li>Jobs</li><li>Terms &amp; Conditions</li></ul>
  <div class="abs foot-divider" style="left:460px"></div>
  <div class="abs foot-head" style="left:525px;top:72px">Contact Us</div>
  <div class="abs foot-rule" style="left:525px;top:101px"></div>
  <div class="abs contact-block">
    <div class="lbl">LOCATION</div>
    <div>418 Orchard Row</div>
    <div>Birchford, VT 05012</div>
    <div style="margin-top:17px"><span class="lbl" style="font-weight:400">Phone :</span> (555) 014-7731</div>
    <div><span class="lbl" style="font-weight:400">Email :</span> info@birchfordpawhaven.com</div>
  </div>
  <div class="abs foot-divider" style="left:727px"></div>
  <div class="abs foot-head" style="left:824px;top:72px">Newsletter Signup</div>
  <div class="abs foot-rule" style="left:824px;top:101px"></div>
  <p class="abs news-copy">If you want receive our all weekly updates about new offers and discount, signup below.</p>
</footer>
<div class="abs news-input">Email Address</div>
<div class="abs news-send"><svg viewBox="0 0 41 35"><path d="M13 18l15-7-5 14-3-5z" fill="#fff"/></svg></div>
<div class="abs copyright">Copyright © 2016, birchfordpawhaven All Rights Reserved</div>
<div class="abs legal-bar"><span>Legal Desclaimer</span><span>Privacy Policy</span><span>Support</span><span>Sitemap</span></div>

</body>
</html>
```